WordPress Design for both website and landing page for an expert

I need a clean and stylish design for my new website. I work as an expert (see attached file WHY HOW WHAT), my product is expert opinion (reports) for company evaluations You can use all of the attached pictures colored or black / white. The person is me, you can add other pictures, if you want. The design should be clean and stylish, so you could use white, black, gray, silver and / or one additional color. I have added an idea about my website, see attached file CONCEPT WEBSITE If you have any more information, please do not hesitate to contact us 'Hesitate to ask me ...

```html
<!DOCTYPE html>
<html lang="de">
<head>
<meta charset="utf-8">
<title>Lukas Brenner – Sachverständiger für Firmenbewertungen</title>
<link rel="stylesheet" href="https://fonts.googleapis.com/css2?family=Montserrat:wght@400;500;600;700&family=Open+Sans:wght@400;600&display=swap">
<style>
:root{
  --black:#000;
  --ink:#111;
  --white:#fff;
  --grey-dark:#3a3a3a;
  --grey-mid:#8a8a8a;
  --grey-light:#f1f1f1;
  --text:#333;
  --head-font:'Montserrat',sans-serif;
  --body-font:'Open Sans',sans-serif;
}
*{box-sizing:border-box;margin:0;padding:0}
html,body{width:1200px;height:4724px;overflow:hidden}
body{font-family:var(--body-font);color:var(--text);background:var(--white);position:relative}
section,header,footer{position:relative;width:1200px;overflow:hidden}

/* hero */
.hero{height:720px;color:var(--white)}
.hero-photo{position:absolute;inset:0;background:linear-gradient(100deg,#2a2a2a 0%,#5d5d5d 35%,#9c9c9c 60%,#6e6e6e 80%,#d0d0d0 100%)}
.hero-shade{position:absolute;inset:0;background:linear-gradient(90deg,rgba(0,0,0,.55),rgba(0,0,0,.1) 70%)}
.topbar{position:absolute;left:0;top:0;width:100%;height:144px;display:flex;align-items:center;justify-content:space-between;padding:0 70px 0 80px}
.brand{font-family:var(--head-font);font-weight:500;font-size:26px;letter-spacing:4px;text-transform:uppercase;color:var(--white);white-space:nowrap}
.nav{display:flex;gap:34px;list-style:none;font-family:var(--head-font);font-weight:600;font-size:17px}
.hero-copy{position:absolute;left:90px;top:350px}
.hero-copy h1{font-family:var(--head-font);font-weight:600;font-size:58px;line-height:1.12}
.hero-copy p{margin-top:38px;font-size:17px}

/* why */
.why{height:568px;background:var(--black);color:var(--white);text-align:center}
.section-title{font-family:var(--head-font);font-weight:600;font-size:38px}
.why .section-title{padding-top:78px}
.hex-row{display:flex;justify-content:center;gap:4px;margin-top:70px}
.hex{position:relative;width:336px;height:296px}
.hex-frame{position:absolute;left:0;top:0}
.hex-content{position:absolute;inset:0;display:flex;flex-direction:column;align-items:center;justify-content:center;padding:0 70px}
.hex-icon{display:block}
.hex-content h3{font-family:var(--head-font);font-weight:700;font-size:30px;margin-top:22px}
.hex-content p{font-size:13px;line-height:1.5;margin-top:10px}

/* uses */
.uses{height:520px;color:var(--white);text-align:center}
.uses-photo{position:absolute;inset:0;background:linear-gradient(160deg,#4d4d4d,#2b2b2b 55%,#5a5a5a)}
.uses .section-title{position:relative;padding-top:90px;font-size:34px}
.use-list{position:relative;list-style:none;margin:70px 0 0 300px;width:620px}
.use-list li{background:var(--white);color:var(--ink);text-align:left;font-family:var(--head-font);font-weight:600;font-size:17px;height:58px;line-height:58px;padding-left:22px;border-radius:4px;margin-bottom:30px}

/* about */
.about{height:472px;display:flex;padding:80px 0 0 88px}
.about-photo{width:384px;height:336px;background:linear-gradient(120deg,#e6e6e6,#bdbdbd 60%,#9a9a9a);border:6px solid var(--white);box-shadow:0 0 0 1px #ccc}
.about-text{margin-left:140px;width:470px;padding-top:10px}
.about-text h2{font-family:var(--head-font);font-weight:600;font-size:40px;color:var(--ink)}
.about-text p{margin-top:34px;font-size:15px;line-height:1.75}

/* promise */
.promise{height:440px;text-align:center}
.promise .brand{display:block;color:var(--grey-mid);font-size:30px;padding-top:84px}
.promise h2{font-family:var(--head-font);font-weight:600;font-size:28px;color:var(--ink);margin-top:70px}
.promise p{font-size:15px;line-height:1.75;margin:22px auto 0;width:640px}

/* process */
.process{height:1040px;background:var(--grey-light)}
.process-line{position:absolute;left:0;top:0}
.step{position:absolute;left:120px;width:960px;height:280px}
.step-text{position:absolute;left:440px;width:480px;text-align:center}
.step-text h3{font-family:var(--head-font);font-weight:600;font-size:38px;color:var(--ink)}
.step-text p{font-size:16px;line-height:1.6;margin:26px auto 0;width:340px}

/* contact */
.contact{height:540px;color:var(--white);text-align:center}
.contact-photo{position:absolute;inset:0;background:linear-gradient(135deg,#2f2f2f,#4b4b4b 50%,#262626)}
.contact .section-title{position:relative;padding-top:90px;font-size:38px}
.form{position:absolute;left:120px;top:180px;width:952px;height:290px}
.field{position:absolute;background:var(--white);color:#777;font-size:12px;text-align:left;padding:8px 10px;border-radius:2px}
.submit{position:absolute;left:408px;top:240px;width:122px;height:44px;background:var(--black);color:var(--white);font-family:var(--head-font);font-weight:600;font-size:17px;border:1px solid #555;line-height:42px}

/* footer */
.footer{height:424px;background:var(--black);color:var(--white)}
.footer .brand{position:absolute;left:130px;top:200px;width:300px;text-align:center;font-size:22px;letter-spacing:3px}
.foot-col{position:absolute;top:96px}
.foot-col h4{font-family:var(--head-font);font-weight:600;font-size:28px}
.foot-links{list-style:none;margin-top:18px;font-size:15px;line-height:1.75}
.newsletter p{margin-top:18px;font-size:14px;line-height:1.5;width:220px}
.news-input{width:210px;height:36px;background:var(--white);color:#777;font-size:11px;padding:10px;margin-top:14px}
.news-btn{width:92px;height:30px;background:var(--white);color:var(--ink);font-size:12px;text-align:center;line-height:30px;border-radius:3px;margin-top:16px}
.copyright{position:absolute;top:368px;width:100%;text-align:center;font-size:13px}
.year{position:absolute;right:30px;top:368px;font-size:13px}
</style>
</head>
<body>

<header class="hero">
  <div class="hero-photo" role="img" aria-label="Portrait of the expert in a suit, standing in a bright office corridor"></div>
  <div class="hero-shade"></div>
  <div class="topbar">
    <span class="brand">Lukas Brenner</span>
    <ul class="nav">
      <li>Home</li><li>What I Do</li><li>Why I Do It &amp; How I Do It</li><li>About Me</li><li>Contact</li>
    </ul>
  </div>
  <div class="hero-copy">
    <h1>Sachverständiger für<br>Firmenbewertungen</h1>
    <p>Sie benötigen ein Gutachten zur Ermittlung des Wertes Ihres Unternehmens</p>
  </div>
</header>

<section class="why">
  <h2 class="section-title">Why you should work with me</h2>
  <div class="hex-row">
    <div class="hex">
      <svg class="hex-frame" viewBox="0 0 336 296" width="336" height="296"><polygon points="84,4 252,4 332,148 252,292 84,292 4,148" fill="none" stroke="#fff" stroke-width="3"/></svg>
      <div class="hex-content">
        <svg class="hex-icon" width="60" height="54" viewBox="0 0 60 54"><path d="M4 26 L56 4 L44 50 L28 34 Z M28 34 L56 4 M28 34 L26 48" fill="none" stroke="#fff" stroke-width="3" stroke-linejoin="round"/></svg>
        <h3>Schnell</h3>
        <p>Sie bekommen Ihr Gutachten zeitnah</p>
      </div>
    </div>
    <div class="hex">
      <svg class="hex-frame" viewBox="0 0 336 296" width="336" height="296"><polygon points="84,4 252,4 332,148 252,292 84,292 4,148" fill="none" stroke="#fff" stroke-width="3"/></svg>
      <div class="hex-content">
        <svg class="hex-icon" width="60" height="60" viewBox="0 0 60 60"><circle cx="30" cy="30" r="25" fill="none" stroke="#fff" stroke-width="3" stroke-dasharray="6 3"/><circle cx="30" cy="30" r="17" fill="none" stroke="#fff" stroke-width="3"/><path d="M22 30 L28 36 L39 24" fill="none" stroke="#fff" stroke-width="3"/></svg>
        <h3>Zertifiziert</h3>
        <p>Sie erhalten ein qualifiziertes und fundiertes Gutachten</p>
      </div>
    </div>
    <div class="hex">
      <svg class="hex-frame" viewBox="0 0 336 296" width="336" height="296"><polygon points="84,4 252,4 332,148 252,292 84,292 4,148" fill="none" stroke="#fff" stroke-width="3"/></svg>
      <div class="hex-content">
        <svg class="hex-icon" width="48" height="60" viewBox="0 0 48 60"><path d="M4 4 H32 L44 16 V56 H4 Z" fill="none" stroke="#fff" stroke-width="3"/><path d="M12 24 H36 M12 32 H36 M12 40 H36 M12 48 H28" stroke="#fff" stroke-width="3"/></svg>
        <h3>Verständlich</h3>
        <p>Ihr Gutachten wird für Sie logisch</p>
      </div>
    </div>
  </div>
</section>

<section class="uses">
  <div class="uses-photo" role="img" aria-label="Dimmed photo of financial charts and a pen on a desk"></div>
  <h2 class="section-title">What do you need or can use a report for</h2>
  <ul class="use-list">
    <li>Buying/selling shares or entire companies</li>
    <li>Inheritance matters</li>
    <li>Questions in gain compensations (in divorce)</li>
  </ul>
</section>

<section class="about">
  <div class="about-photo" role="img" aria-label="Photo of the expert seated at a table by a window"></div>
  <div class="about-text">
    <h2>About Me</h2>
    <p>Lassen Sie Ihr Unternehmen von einem qualifizierten Sachverständigen bewerten und gehen somit vielen (unnötigen) Streitereien aus dem Weg. Merke: Die Kosten für ein Gutachten sind immer überproportional günstiger als die Kosten für Rechtsstreitigkeiten. Und das losgelöst von der psychischen Belastung einer solchen Auseinandersetzung…</p>
  </div>
</section>

<section class="promise">
  <span class="brand">Lukas Brenner</span>
  <h2>Mein Qualitätsversprechen:</h2>
  <p>Sollte der avisierte Termin für die Erstellung des Gutachtens überschritten werden, erhalten Sie das Gutachten absolut kostenfrei!<br>(ich verzichte auf mein Honorar)</p>
</section>

<section class="process">
  <svg class="process-line" width="1200" height="1040" viewBox="0 0 1200 1040">
    <line x1="260" y1="360" x2="260" y2="400" stroke="#555" stroke-width="3" stroke-dasharray="4 6"/>
    <line x1="260" y1="680" x2="260" y2="720" stroke="#555" stroke-width="3" stroke-dasharray="4 6"/>
    <g font-family="Montserrat, sans-serif" font-weight="700" font-size="34" text-anchor="middle">
      <g transform="translate(260,220)">
        <circle r="140" fill="#000"/><circle r="118" fill="none" stroke="#fff" stroke-width="4"/><circle r="92" fill="#fff"/>
        <text y="12" fill="#000">WHAT</text>
      </g>
      <g transform="translate(260,540)">
        <circle r="140" fill="#000"/><circle r="118" fill="none" stroke="#fff" stroke-width="4"/><circle r="92" fill="#fff"/>
        <text y="12" fill="#000">HOW</text>
      </g>
      <g transform="translate(260,860)">
        <circle r="140" fill="#000"/><circle r="118" fill="none" stroke="#fff" stroke-width="4"/><circle r="92" fill="#fff"/>
        <text y="12" fill="#000">WHY</text>
      </g>
    </g>
  </svg>
  <div class="step" style="top:120px">
    <div class="step-text"><h3>What I do</h3><p>Conducting business valuations in case of… Durchführung von Unternehmensbewertungen (Wertermittlung) bei:</p></div>
  </div>
  <div class="step" style="top:440px">
    <div class="step-text"><h3>How I do, what I do</h3><p>Jedes Gutachten beginnt mit Verstehen. Also stelle ich Ihnen Fragen und höre sehr genau zu.</p></div>
  </div>
  <div class="step" style="top:760px">
    <div class="step-text"><h3>Why I do, what I do</h3><p>Economy is my passion. Economy is made in numbers. Sometimes it is difficult to find the right numbers.</p></div>
  </div>
</section>

<section class="contact">
  <div class="contact-photo" role="img" aria-label="Dark photo of documents with charts and a calculator"></div>
  <h2 class="section-title">Contact Us</h2>
  <div class="form">
    <div class="field" style="left:0;top:0;width:472px;height:36px">Name</div>
    <div class="field" style="left:488px;top:0;width:464px;height:36px">Email</div>
    <div class="field" style="left:0;top:50px;width:472px;height:36px">Phone Number</div>
    <div class="field" style="left:488px;top:50px;width:464px;height:36px">Appointments</div>
    <div class="field" style="left:0;top:100px;width:952px;height:108px">Message</div>
    <div class="submit">Submit</div>
  </div>
</section>

<footer class="footer">
  <span class="brand">Lukas Brenner</span>
  <div class="foot-col" style="left:488px">
    <h4>Quick Link</h4>
    <ul class="foot-links"><li>Home</li><li>What I Do</li><li>Why I Do It &amp; How I Do It</li><li>About Me</li><li>Contact</li></ul>
  </div>
  <div class="foot-col newsletter" style="left:760px">
    <h4>Newsletter</h4>
    <p>Register your email for news for Lukas Brenner</p>
    <div class="news-input">Enter the email</div>
    <div class="news-btn">Subscribe</div>
  </div>
  <div class="copyright">Copyright © 2018 Lukas Brenner All Rights Reserved.</div>
  <div class="year">2018</div>
</footer>

</body>
</html>
```